veLuna - nutrition bars - logo and packaging*

veLuna develops stress-relief nutrition bars powered by deep profiling machine learning technology, offering personalized stress management routine.
We produce 3 flavors of nutrition bars. in each flavor, we produce 6 stress relief formulations (3 for day, 3 for night) in 2 strengths.

We need a rebranding of our logo and packaging.

Target Market(s)

Full description of the target audience and their needs and lifestyle is explained in the attached presentation

Logo Text

veLuna

Font styles to use
Script

Colors

Designer to choose colors to be used in the design.

Requirements
Must have
• logo
• Packaging
• Full description of the deliveries is explained in the attached presentation
Nice to have
• concept for boxes, website

```html
<!DOCTYPE html>
<html lang="en">
<head>
<meta charset="utf-8">
<title>veLuna – Stress-relief bar wrappers</title>
<link href="https://fonts.googleapis.com/css2?family=Lato:wght@400;700;900&display=swap" rel="stylesheet">
<style>
  :root{
    --bg:#ffffff;
    --wrap-black:#0d0d0d;
    --white:#ffffff;
    --green:#2f7b2c;
    --blue:#4b60b0;
    --pink:#c63c79;
    --gray:#8d99a2;
    --gray-soft:#dfe4e8;
  }
  *{box-sizing:border-box;margin:0;padding:0}
  html,body{width:1200px;height:857px;overflow:hidden;background:var(--bg)}
  body{font-family:"Lato",sans-serif;position:relative}

  .wrapper{
    position:absolute;top:65px;width:265px;height:725px;
    background:var(--wrap-black);overflow:hidden;color:var(--white);
  }
  .wrapper--calm{left:40px;--tone:var(--green)}
  .wrapper--comfort{left:325px;--tone:var(--blue)}
  .wrapper--energy{left:612px;--tone:var(--pink)}
  .wrapper--sleep{left:898px;--tone:var(--gray)}

  .crimp{
    position:absolute;left:0;right:0;height:34px;
    background:repeating-linear-gradient(180deg,rgba(255,255,255,.10) 0 2px,transparent 2px 6px);
  }
  .crimp--top{top:0}
  .crimp--bottom{bottom:0;z-index:2}

  .brand{position:absolute;top:138px;left:0;right:0;text-align:center}
  .brand__name{font-weight:900;font-size:54px;letter-spacing:-.5px;line-height:1}
  .brand__tagline{display:block;text-align:right;padding-right:22px;margin-top:4px;font-size:12px;font-weight:400}

  .panel{
    position:absolute;left:-20px;right:-20px;top:222px;bottom:0;
    background:var(--tone);border-radius:50% 50% 0 0 / 16px 16px 0 0;
  }

  .motif{
    position:absolute;left:50%;transform:translateX(-50%);top:315px;
    width:130px;height:130px;border-radius:10px;
    background:radial-gradient(circle,rgba(255,255,255,.22),rgba(255,255,255,.06));
  }
  .wrapper--comfort .motif{width:190px;height:120px;top:325px}
  .wrapper--energy .motif{width:110px;height:190px;top:300px}
  .wrapper--sleep .motif{width:190px;height:150px;top:305px;background:radial-gradient(circle,rgba(0,0,0,.2),rgba(0,0,0,.05))}

  .time-icon{position:absolute;left:50%;transform:translateX(-50%);top:512px;width:34px;height:30px}
  .time-icon--dark{color:var(--wrap-black)}

  .variant{
    position:absolute;left:50%;transform:translateX(-50%);top:547px;
    height:30px;padding:0 16px;border-radius:15px;white-space:nowrap;
    font-size:15px;font-weight:700;line-height:30px;letter-spacing:.3px;
  }
  .variant--light{background:var(--white);color:var(--tone)}
  .variant--dark{background:var(--wrap-black);color:var(--tone)}
  .wrapper--sleep .variant--dark{color:var(--gray-soft)}

  .info{position:absolute;left:0;right:0;top:585px;text-align:center}
  .info__claim{font-size:14px}
  .info__flavor{font-size:18px;font-weight:700;margin-top:9px;opacity:.85}
  .info__flavor--small{font-size:14px;font-weight:400;margin-top:9px}
  .info__weight{display:block;text-align:left;padding-left:50px;font-size:14px;opacity:.8}
  .wrapper--sleep .info__flavor,.wrapper--sleep .info__weight{color:var(--gray-soft)}
</style>
</head>
<body>

<article class="wrapper wrapper--calm">
  <div class="crimp crimp--top"></div>
  <div class="brand"><div class="brand__name">veLuna</div><span class="brand__tagline">Gentle Daily Ritual</span></div>
  <div class="panel"></div>
  <div class="motif" role="img" aria-label="Line drawing of a closed lotus bud"></div>
  <svg class="time-icon" viewBox="0 0 34 30" fill="none" stroke="#fff" stroke-width="2.2" stroke-linecap="round"><path d="M9 22a8 8 0 0 1 16 0"/><path d="M2 22h6M26 22h6M17 4v6M6 9l4 4M28 9l-4 4M12 26h10"/></svg>
  <div class="variant variant--light">SERENE GREEN</div>
  <div class="info"><p class="info__claim">Natural terpenes</p><p class="info__flavor">Dates, Apples &amp; Nuts</p><span class="info__weight">30 gr</span></div>
  <div class="crimp crimp--bottom"></div>
</article>

<article class="wrapper wrapper--comfort">
  <div class="crimp crimp--top"></div>
  <div class="brand"><div class="brand__name">veLuna</div><span class="brand__tagline">Gentle Daily Ritual</span></div>
  <div class="panel"></div>
  <div class="motif" role="img" aria-label="Line drawing of an open lotus flower"></div>
  <svg class="time-icon time-icon--dark" viewBox="0 0 34 30" fill="currentColor"><path d="M15 4a11 11 0 1 0 12 15A9 9 0 0 1 15 4z"/><path d="M26 3l1 3 3 1-3 1-1 3-1-3-3-1 3-1zM30 12l.6 1.6 1.6.6-1.6.6-.6 1.6-.6-1.6-1.6-.6 1.6-.6z"/></svg>
  <div class="variant variant--dark">COZY NIGHT BLUE+</div>
  <div class="info"><p class="info__claim">Natural terpenes &amp; herbs</p><p class="info__flavor">Dates, Apples &amp; Nuts</p><span class="info__weight">30 gr</span></div>
  <div class="crimp crimp--bottom"></div>
</article>

<article class="wrapper wrapper--energy">
  <div class="crimp crimp--top"></div>
  <div class="brand"><div class="brand__name">veLuna</div><span class="brand__tagline">Gentle Daily Ritual</span></div>
  <div class="panel"></div>
  <div class="motif" role="img" aria-label="Line drawing of a single curved wheat stalk"></div>
  <svg class="time-icon" viewBox="0 0 34 30" fill="none" stroke="#fff" stroke-width="2.2" stroke-linecap="round"><path d="M9 22a8 8 0 0 1 16 0"/><path d="M2 22h6M26 22h6M17 4v6M6 9l4 4M28 9l-4 4M12 26h10"/></svg>
  <div class="variant variant--light">BRIGHT PINK</div>
  <div class="info"><p class="info__claim">Natural terpenes &amp; herbs</p><p class="info__flavor info__flavor--small">Oats, cranberries &amp; chocolate</p><span class="info__weight">30 gr</span></div>
  <div class="crimp crimp--bottom"></div>
</article>

<article class="wrapper wrapper--sleep">
  <div class="crimp crimp--top"></div>
  <div class="brand"><div class="brand__name">veLuna</div><span class="brand__tagline">Gentle Daily Ritual</span></div>
  <div class="panel"></div>
  <div class="motif" role="img" aria-label="Line drawing of two wheat stalks joined in an arc"></div>
  <svg class="time-icon time-icon--dark" viewBox="0 0 34 30" fill="currentColor"><path d="M15 4a11 11 0 1 0 12 15A9 9 0 0 1 15 4z"/><path d="M26 3l1 3 3 1-3 1-1 3-1-3-3-1 3-1zM30 12l.6 1.6 1.6.6-1.6.6-.6 1.6-.6-1.6-1.6-.6 1.6-.6z"/></svg>
  <div class="variant variant--dark">DREAMY GRAY+</div>
  <div class="info"><p class="info__claim">Natural terpenes &amp; herbs</p><p class="info__flavor info__flavor--small">Oats, cranberries &amp; chocolate</p><span class="info__weight">30 gr</span></div>
  <div class="crimp crimp--bottom"></div>
</article>

</body>
</html>
```